Wordpress Web Design & Coding for velcorahealth.ca

We need a website for a new investment company that is visually grabbing and vibrant. We would like to see a web page that displays trust, growth and confidence. Needs to be responsive and mobile friendly for all browsers and coded for both Android & IOS.

Open to the number of pages and menu items. I selected 4 but if you feel the layout would work better with less I am open to this. Need to sell the people (management team/related businesses) and then show where the invested money will be going (upcoming projects).

Company Info:

Vel Cora is an investment company put together by a group of seasoned business professionals who have come together to combine decades of success in the real estate development, management, financing and medical services. The company will be a full service company offering turn key solutions for medical professionals.

Vel-Cora will focus on providing a full range of services via a group of distinct companies to deliver newly emerging needs of the medical community. The end goal will be to create complete solutions for individuals in the medical community. Our group has experience and success with the conceptualization, construction and financing of medical and dental clinic spaces. Vel-Cora Solutions will be established to accommodate all areas of the development and creation of clinics for medical professionals from building construction to equipment financing and administrations.

You can mention these companies and take photos from their websites. You can also use stock photos.

Our construction partner:
https://318bld.com/projects/

Our equipment leasing partner:
https://www.norvixa.com/

Our Management Team and medical partners

Gil Parish
https://www.ourfirmstance.ca/

Dietmar Vellasquin
https://www.gshdentalservices.com/about-us

PROPOSED PROJECTS (see attachment for details)
Pinegrove Business Park
Holtmere Business Park
Mt. Corwin Ridge Professional

Target Market(s)

Investors

Industry/Entity Type

Investment

Coding

Coded - Design and coding required

Number of Pages Required

4 page

Font styles to use
Sans Serif

Requirements
Must have
• Wordpress – must be both desktop and mobile friendly with fast page load speed
Ability to edit after ourselves in Wordpress
Attractive home page with logo etc.
Logo colours are: for the blue the pantone color is #0355a3
and for the green is #8cc63f

Sections, about us, what we do/services we provide, contact us

```html
<!DOCTYPE html>
<html lang="en">
<head>
<meta charset="utf-8">
<title>Vel-Cora Solutions — Partners</title>
<link href="https://fonts.googleapis.com/css2?family=Montserrat:wght@300;400;500;600;700;800&display=swap" rel="stylesheet">
<style>
:root{
  --blue:#1f5aa6;
  --blue-dark:#174c91;
  --green:#8cc63f;
  --ink:#111;
  --muted:#7a7a7a;
  --card:#f3f3f3;
  --rule:#e6e6e6;
  --orange:#f5a31a;
  --logo-green:#1d6b2a;
}
*{margin:0;padding:0;box-sizing:border-box}
html,body{width:961px;height:1200px;overflow:hidden}
body{font-family:'Montserrat',sans-serif;color:var(--ink);background:#fff;position:relative}
.hero{position:absolute;left:0;top:0;width:961px;height:216px;background:linear-gradient(180deg,var(--blue) 0%,var(--blue-dark) 100%);}
.hero-photo{position:absolute;inset:0;background:linear-gradient(180deg,rgba(255,255,255,.08),rgba(255,255,255,0) 60%,rgba(255,255,255,.06));}
.hero-text{position:absolute;left:0;right:0;top:4px;text-align:center;color:#fff;font-weight:800;font-size:19px;line-height:30px}
.grid-line{position:absolute;top:216px;height:575px;width:1px;background:var(--rule)}
.section-label{position:absolute;left:188px;font-size:8px;font-weight:700;letter-spacing:.1px}
.see-all{position:absolute;right:187px;top:284px;font-size:7px;color:var(--muted)}
.card{position:absolute;height:135px;background:var(--card)}
.card-photo{position:absolute;left:0;top:0;width:100px;height:135px}
.card-body{position:absolute;left:112px;top:10px;right:10px}
.card-kind{font-size:7px;color:var(--muted);font-weight:400}
.card-title{font-size:10px;font-weight:700;margin-top:6px}
.card-title.accent{color:var(--orange)}
.card-desc{font-size:7.4px;line-height:12px;color:var(--muted);font-weight:400;margin-top:8px;height:48px;overflow:hidden}
.card-link{position:absolute;left:112px;top:114px;font-size:7.4px;color:var(--ink)}
.card-link.underlined{text-decoration:underline}
.contact{position:absolute;left:0;top:796px;width:961px;height:404px;background:var(--green);text-align:center}
.eyebrow{position:absolute;left:0;right:0;top:93px;font-size:7px;font-weight:700;letter-spacing:.3px}
.email{position:absolute;left:0;right:0;top:110px;font-size:30px;font-weight:800;letter-spacing:-.3px}
.address{position:absolute;left:0;right:0;top:158px;font-size:12px;font-weight:600;line-height:20px}
.social{position:absolute;left:0;right:0;top:245px;font-size:8.5px}
.social a{color:var(--ink);text-decoration:none;margin:0 7px}
.social a.active{text-decoration:underline}
.copyright{position:absolute;left:0;right:0;top:270px;font-size:8px}
.brand{position:absolute;left:0;right:0;top:326px;display:flex;justify-content:center;align-items:center;gap:5px}
.brand-mark{width:11px;height:11px;background:var(--logo-green)}
.brand-name{font-size:10px;font-weight:700;color:var(--logo-green)}
</style>
</head>
<body>
<header class="hero">
  <div class="hero-photo" role="img" aria-label="Blue-toned photo of a business park building with parked cars"></div>
  <p class="hero-text">services that are ongoing at this time. One of our<br>strategic goals is to assist the medical community<br>in catering to those services.</p>
</header>

<div class="grid-line" style="left:188px"></div>
<div class="grid-line" style="left:384px"></div>
<div class="grid-line" style="left:579px"></div>
<div class="grid-line" style="left:773px"></div>

<h2 class="section-label" style="top:283px">PARTNERS</h2>
<a class="see-all">See all partners</a>

<article class="card" style="left:188px;top:334px;width:285px">
  <div class="card-photo" role="img" aria-label="Photo of a three-storey office building under blue sky" style="background:linear-gradient(180deg,#3f6fc4 0%,#e9ecef 45%,#8f9297 100%)"></div>
  <div class="card-body">
    <p class="card-kind">Construction Partner</p>
    <h3 class="card-title accent">318 BUILDERS INC.</h3>
    <p class="card-desc">318 Builders has a broad range of experience providing design, construction services and interior improvements for com-mercial office and warehouse buildings</p>
  </div>
  <a class="card-link underlined">Learn More</a>
</article>

<article class="card" style="left:488px;top:334px;width:286px">
  <div class="card-photo" role="img" aria-label="Photo of a white handheld medical device" style="background:linear-gradient(135deg,#f4f1ec 0%,#e2d9cf 60%,#c9b7a6 100%)"></div>
  <div class="card-body">
    <p class="card-kind">Equipment Leasing Partner</p>
    <h3 class="card-title">Norvixa Equipment Leasing Inc.</h3>
    <p class="card-desc">Small business owners need fast answers. We pride ourselves on being customer focused and responsive to your needs. You can expect</p>
  </div>
  <a class="card-link">Learn More</a>
</article>

<h2 class="section-label" style="top:519px">MANAGEMENT TEAM AND MEDICAL PARTNERS</h2>

<article class="card" style="left:188px;top:570px;width:285px">
  <div class="card-photo" role="img" aria-label="Portrait photo of Dr. Gil Parish" style="background:linear-gradient(180deg,#6d6a68 0%,#8d8480 50%,#5b5a5c 100%)"></div>
  <div class="card-body">
    <p class="card-kind">Medical Partner</p>
    <h3 class="card-title">Dr. Gil Parish</h3>
    <p class="card-desc">A published author and experienced, board-certified physician in the field of Bioidentical Hormone Replacement Therapy, Dr. Parish believes in a holistic approach to</p>
  </div>
  <a class="card-link underlined">Learn More</a>
</article>

<article class="card" style="left:488px;top:570px;width:286px">
  <div class="card-photo" role="img" aria-label="Portrait photo of Dietmar Vellasquin outdoors by the sea" style="background:linear-gradient(180deg,#c9d6dd 0%,#4bb0b3 45%,#3a3030 100%)"></div>
  <div class="card-body">
    <p class="card-kind">Equipment Leasing Partner</p>
    <h3 class="card-title">Dietmar Vellasquin</h3>
    <p class="card-desc">Dietmar brings more than 25 years of experi-ence working with dentists across Western Canada as an equipment specialist and a</p>
  </div>
  <a class="card-link">Learn More</a>
</article>

<footer class="contact">
  <p class="eyebrow">LET’S WORK TOGETHER</p>
  <p class="email">hello@vel-cora.com</p>
  <p class="address">27 Lindell Row, 9th Floor . Brantmoor, Alberta, Canada<br>(+012) 555-0148-00</p>
  <nav class="social">
    <a>Skylark</a><a class="active">Gatherly</a><a>Folioz</a><a>Pixelrun</a>
  </nav>
  <p class="copyright">© 2020 Vel-Cora. All Right Reserved</p>
  <div class="brand"><span class="brand-mark"></span><span class="brand-name">VEL-CORA</span></div>
</footer>
</body>
</html>
```